Brintel Works - Fast, Efficient and Gas Mainteance for Domestic, Commercial and Industrial clients

We are in the process of purchasing a new business and would like to get a new logo and business card.
Business is a gas maintenance business that also does new gas installations.
Has been established since 1988.
Services include:
Install all types of gas appliances & equipment inc. hot water units
Maintain / repair / replace all types of gas appliances & equipment

Target Market(s)

Domestic, Commercial and Industrial clients

Industry/Entity Type

Business

Contact Information for Business Card

admin@brintelworks.com.au
07 3918 4726
Brintel Works PTY LTD

Logo Text

Gas Fitting & Plumbing Maintenance Specialists

Font styles to use
Sans Serif

Requirements
Must have
• Logo
• Business name, contact number, email address, web address
• Domestic | Commercial | Industrial Est Since 1988
Nice to have
• Possibly a black card with a flame logo to one side
Should not have
• Spelling errors

```html
<!DOCTYPE html>
<html lang="en">
<head>
<meta charset="utf-8">
<title>Brintel Works – Business Card</title>
<link href="https://fonts.googleapis.com/css2?family=Source+Sans+3:wght@400;600&display=swap" rel="stylesheet">
<style>
  :root {
    --backdrop: #3a3330;
    --card: #141414;
    --brand-yellow: #f2d21b;
    --brand-red: #e8262b;
    --accent-orange: #f0891f;
    --text-white: #f4f4f4;
  }
  * { margin: 0; padding: 0; box-sizing: border-box; }
  html, body {
    width: 1200px; height: 844px; overflow: hidden;
    background: var(--backdrop);
    font-family: "Source Sans 3", Arial, sans-serif;
  }
  .stage {
    position: relative; width: 1200px; height: 844px;
    display: flex; align-items: center; justify-content: center; gap: 40px;
  }
  .card {
    position: relative; width: 520px; height: 316px;
    background: var(--card);
    border-radius: 3px;
    box-shadow: 0 8px 24px rgba(0,0,0,.45);
  }
  .brand {
    position: absolute;
    display: flex; align-items: center; gap: 14px;
  }
  .brand-dot {
    width: 22px; height: 22px; border-radius: 50%;
    background: var(--brand-red);
  }
  .brand-name {
    color: var(--brand-yellow);
    font-weight: 400; font-size: 46px; line-height: 1;
    letter-spacing: .5px;
  }
  .brand-suffix {
    color: var(--brand-yellow);
    font-weight: 400; font-size: 15px; letter-spacing: 4px;
    position: absolute;
  }

  /* Front: contact face */
  .card--front .brand { left: 58px; top: 92px; }
  .card--front .brand-suffix { left: 94px; top: 150px; }
  .contact-list {
    position: absolute; right: 36px; top: 170px;
    list-style: none; text-align: right;
    color: var(--text-white); font-size: 14px; line-height: 23px;
  }
  .contact-list li { display: flex; justify-content: flex-end; align-items: center; gap: 10px; }
  .contact-list svg { width: 12px; height: 12px; fill: none; stroke: var(--accent-orange); stroke-width: 1.6; }
  .address {
    position: absolute; left: 36px; bottom: 34px;
    color: var(--text-white); font-size: 16px; line-height: 24px;
  }

  /* Back: brand face */
  .card--back .brand { left: 70px; top: 100px; }
  .card--back .brand-suffix { left: 106px; top: 158px; }
  .tagline {
    position: absolute; left: 0; right: 0; top: 222px;
    text-align: center; color: var(--accent-orange);
    font-size: 15px; font-weight: 600;
  }
</style>
</head>
<body>
<main class="stage">
  <section class="card card--front" aria-label="Business card front">
    <div class="brand">
      <span class="brand-dot"></span>
      <span class="brand-name">Brintel Works</span>
    </div>
    <span class="brand-suffix">PTY LTD</span>
    <ul class="contact-list">
      <li>07 3918 4726
        <svg viewBox="0 0 12 12" aria-hidden="true"><path d="M2 1.5l2 0 1 2.5-1.3 1a6 6 0 0 0 3.3 3.3l1-1.3 2.5 1v2a1 1 0 0 1-1 1A9.5 9.5 0 0 1 1 2.5a1 1 0 0 1 1-1z"/></svg>
      </li>
      <li>admin@brintelworks.com.au
        <svg viewBox="0 0 12 12" aria-hidden="true"><rect x="1" y="2.5" width="10" height="7"/><path d="M1 2.5l5 4 5-4"/></svg>
      </li>
      <li>www.brintelworks.com.au
        <svg viewBox="0 0 12 12" aria-hidden="true"><path d="M5 7l2-2M4.5 5.5l-2 2a1.8 1.8 0 0 0 2.5 2.5l2-2M7.5 6.5l2-2A1.8 1.8 0 0 0 7 2l-2 2"/></svg>
      </li>
    </ul>
    <p class="address">12345, Address Goes Here<br>Country Name, 123456</p>
  </section>

  <section class="card card--back" aria-label="Business card back">
    <div class="brand">
      <span class="brand-dot"></span>
      <span class="brand-name">Brintel Works</span>
    </div>
    <span class="brand-suffix">PTY LTD</span>
    <p class="tagline">Domestic | Commercial | Industrial Est Since 1988</p>
  </section>
</main>
</body>
</html>
```